Audio/ Video Packaging Design for a Technology company.

We need a packaging design for a bag that is 7" wide and 10" high. The design will be for a new line of audio/video products. We would like to see designs that represent a superior quality product that provides a pure connection. We want the equivalent of a nice retail bag that you would find in a store like Tallow Mart. It should be a maximum of three colors. We really want something sharp, professional and eye catching, not whimsical or cartoonish. I've included a couple of examples below. I don't really like the designs of the bags, but I want you to see examples of what I'm looking for.

The company logo, which is uploaded, should be on the design. The words "audio and video products" should be either underneath the logo or to the side. Also, somewhere on the bag, we would like the words "For a Pure Connection"

The winner of this contest will likely get the opportunity for additional work as we have more products ready to launch.

Target Market(s)

resellers, consumers - men 25-60

Industry/Entity Type

It Company

Requirements
Must have
• It should be a maximum of three colors. We really want something sharp, professional and eye catching, not whimsical or cartoonish
Nice to have
• Eye-catching design. Utilize the entire bag but don't make it too busy.
Should not have
• Whimsical, cartoonish

```html
<!DOCTYPE html>
<html lang="en">
<head>
<meta charset="utf-8">
<title>Veralink Package Design</title>
<link href="https://fonts.googleapis.com/css2?family=Montserrat:wght@400;500;600;700&display=swap" rel="stylesheet">
<style>
:root{
  --stage:#8a8a8a;
  --ink:#262a30;
  --charcoal:#3d3d3f;
  --sky:#5bc0ee;
  --royal:#2f74c8;
  --paper:#ffffff;
  --pane-light:#f1f1f1;
  --pane-mid:#c9c9c9;
  --muted:#9a9a9a;
}
*{margin:0;padding:0;box-sizing:border-box}
html,body{width:1200px;height:960px;overflow:hidden}
body{background:var(--stage);font-family:"Montserrat",sans-serif;position:relative}
.presentation-title{position:absolute;right:54px;top:52px;text-align:right}
.brand-name{font-weight:500;letter-spacing:3px;color:var(--ink);display:inline-flex;align-items:center;gap:10px;line-height:1}
.brand-name .brand-square{width:.55em;height:.55em;background:var(--sky);display:inline-block}
.presentation-title .brand-name{font-size:46px}
.presentation-title .caption{color:#e9e9e9;font-weight:500;font-size:22px;letter-spacing:1px;margin-top:22px}
.presentation-title .size{color:#fafafa;font-weight:600;font-size:17px;margin-top:6px}
.bag{position:absolute;top:324px;width:364px;height:542px}
.bag svg{position:absolute;inset:0}
.bag--brand{left:26px}
.bag--power{left:418px}
.bag--hdmi{left:806px}
.made-in{position:absolute;left:14px;font-size:7px;letter-spacing:.5px;color:var(--muted);writing-mode:vertical-rl;transform:rotate(180deg)}
.tagline{position:absolute;width:100%;text-align:center;color:var(--paper);font-size:17px;font-weight:500;letter-spacing:.5px}
.subline{font-size:13.5px;letter-spacing:2.4px;color:var(--sky);font-weight:500}
.lockup-bottom{position:absolute;right:30px;top:424px;text-align:right}
.lockup-bottom .brand-name{color:var(--paper);font-size:36px}
.lockup-bottom .subline{margin-top:8px}
.lockup-window{position:absolute;left:70px;top:100px;text-align:center;width:232px}
.lockup-window .brand-name{font-size:36px}
.pill{display:inline-block;background:var(--ink);color:var(--sky);border-radius:3px;padding:2px 7px;margin-top:6px;font-size:13.5px;letter-spacing:1.8px}
.lockup-top{position:absolute;left:0;width:100%;top:78px;text-align:center}
.lockup-top .brand-name{font-size:36px}
.lockup-top .subline{margin-top:6px;color:var(--sky)}
.spec{position:absolute;left:18px;top:410px;display:flex;align-items:flex-end;gap:4px}
.spec-type{writing-mode:vertical-rl;transform:rotate(180deg);font-weight:600;font-size:19px;letter-spacing:1px;padding:3px 2px;line-height:1}
.spec-type--power{background:var(--sky);color:var(--charcoal)}
.spec-type--hdmi{background:var(--paper);color:var(--ink);letter-spacing:4px}
.spec-value{writing-mode:vertical-rl;transform:rotate(180deg);font-size:12px;color:var(--paper);font-weight:500;line-height:1}
.spec-value--power{color:var(--sky)}
.product-word{position:absolute;left:68px;top:440px;font-weight:700;font-size:58px;color:var(--sky);letter-spacing:1px;line-height:1;border-bottom:2px solid var(--sky);padding-bottom:1px}
.bag--power .tagline,.bag--hdmi .tagline{top:504px}
.bag--brand .tagline{top:500px}
</style>
</head>
<body>

<header class="presentation-title">
  <div class="brand-name"><span class="brand-square"></span>VERALINK</div>
  <p class="caption">PACKAGE DESIGN</p>
  <p class="size">SIZE : 7” (W) X 10” (H)</p>
</header>

<!-- Brand bag -->
<section class="bag bag--brand">
  <svg viewBox="0 0 364 542" width="364" height="542">
    <defs>
      <clipPath id="bag-a"><rect width="364" height="542" rx="24"/></clipPath>
      <linearGradient id="pane-a" x1="0" y1="0" x2="1" y2="1">
        <stop offset="0" stop-color="var(--pane-mid)"/><stop offset=".5" stop-color="var(--pane-light)"/><stop offset="1" stop-color="var(--pane-mid)"/>
      </linearGradient>
    </defs>
    <g clip-path="url(#bag-a)">
      <rect width="364" height="542" fill="var(--paper)"/>
      <line x1="8" y1="72" x2="356" y2="72" stroke="#e6e6e6" stroke-dasharray="4 3"/>
      <rect x="33" y="80" width="298" height="360" rx="22" fill="url(#pane-a)" stroke="#9a9a9a"/>
      <polygon points="0,215 218,400 364,165 364,186 218,420 0,232" fill="var(--sky)"/>
      <polygon points="0,232 218,420 364,186 364,542 0,542" fill="var(--charcoal)"/>
      <polygon points="0,240 218,430 364,194 364,198 218,434 0,244" fill="var(--paper)"/>
    </g>
  </svg>
  <span class="made-in" style="top:450px">MADE IN CHINA</span>
  <div class="lockup-bottom">
    <div class="brand-name"><span class="brand-square"></span>VERALINK</div>
    <div class="subline">audio and video products</div>
  </div>
  <p class="tagline">“For a Pure Connection”</p>
</section>

<!-- Power cable bag -->
<section class="bag bag--power">
  <svg viewBox="0 0 364 542" width="364" height="542">
    <defs>
      <clipPath id="bag-b"><rect width="364" height="542" rx="24"/></clipPath>
      <linearGradient id="pane-b" x1="0" y1="0" x2="1" y2="1">
        <stop offset="0" stop-color="var(--pane-mid)"/><stop offset=".5" stop-color="var(--pane-light)"/><stop offset="1" stop-color="var(--pane-mid)"/>
      </linearGradient>
    </defs>
    <g clip-path="url(#bag-b)">
      <rect width="364" height="542" fill="var(--paper)"/>
      <line x1="8" y1="72" x2="356" y2="72" stroke="#e6e6e6" stroke-dasharray="4 3"/>
      <rect x="40" y="86" width="284" height="360" rx="22" fill="url(#pane-b)" stroke="#8a8a8a"/>
      <polygon points="0,235 225,416 364,180 364,200 225,436 0,252" fill="var(--royal)"/>
      <polygon points="0,252 225,436 364,200 364,542 0,542" fill="var(--charcoal)"/>
      <polygon points="0,260 225,446 364,208 364,212 225,450 0,264" fill="var(--paper)"/>
    </g>
  </svg>
  <div class="lockup-window">
    <div class="brand-name"><span class="brand-square"></span>VERALINK</div>
    <div class="pill">audio and video products</div>
  </div>
  <span class="made-in" style="top:344px;left:20px">MADE IN CHINA</span>
  <div class="spec">
    <span class="spec-type spec-type--power">POWER</span>
    <span class="spec-value spec-value--power">110V ~300V</span>
  </div>
  <div class="product-word">CABLE</div>
  <p class="tagline">“For a Pure Connection”</p>
</section>

<!-- HDMI cable bag -->
<section class="bag bag--hdmi">
  <svg viewBox="0 0 364 542" width="364" height="542">
    <defs>
      <clipPath id="bag-c"><rect width="364" height="542" rx="24"/></clipPath>
      <linearGradient id="pane-c" x1="0" y1="0" x2="1" y2="1">
        <stop offset="0" stop-color="var(--pane-mid)"/><stop offset=".5" stop-color="var(--pane-light)"/><stop offset="1" stop-color="var(--pane-mid)"/>
      </linearGradient>
    </defs>
    <g clip-path="url(#bag-c)">
      <rect width="364" height="542" fill="var(--paper)"/>
      <line x1="8" y1="72" x2="356" y2="72" stroke="#e6e6e6" stroke-dasharray="4 3"/>
      <rect x="40" y="145" width="284" height="320" rx="22" fill="url(#pane-c)" stroke="#9a9a9a"/>
      <polygon points="0,232 222,410 364,180 364,200 222,430 0,250" fill="var(--royal)"/>
      <polygon points="0,250 222,430 364,200 364,542 0,542" fill="var(--charcoal)"/>
      <polygon points="0,258 222,440 364,208 364,212 222,444 0,262" fill="var(--paper)"/>
    </g>
  </svg>
  <div class="lockup-top">
    <div class="brand-name"><span class="brand-square"></span>VERALINK</div>
    <div class="subline">audio and video products</div>
  </div>
  <span class="made-in" style="top:344px;left:20px">MADE IN CHINA</span>
  <div class="spec">
    <span class="spec-type spec-type--hdmi">HDMI</span>
    <span class="spec-value">1.4 | 10.2 Gbps</span>
  </div>
  <div class="product-word">CABLE</div>
  <p class="tagline">“For a Pure Connection”</p>
</section>

</body>
</html>
```